Business card design Needed for new logo / Construction business, home extensions and new builds

We need a business card design using our new logo files which i will attach to this project :)

We are a small construction business specialising in home extensions, new builds and property development. We are very ambitious and would appreciate professional and elegant designs for our new business card.

Very serious about using the services on MakerQuarry and recently acquired our new logo from here :)

Please get involved, i will feedback when i can as i am very busy but can respond daily, thanks

Target Market(s)

People that want to build onto their houses, new building developments or adding too their existing property

Industry/Entity Type

Construction

Contact Information for Business Card

Renwick Tolliver Construction, Lionel Ashby (Managing Director), Tel 07822254961, email - info@renwick-tolliver, www.renwick-tolliver.co.uk

Colors

Designer to choose colors to be used in the design.

Requirements
Must have
• I like a deep grey on the back please. A lot of you have provided black from and back, try mixing things up a little. The black looks cool 😎 Thanks

```html
<!DOCTYPE html>
<html lang="en">
<head>
<meta charset="utf-8">
<title>Renwick Tolliver Construction – Business Card</title>
<link rel="stylesheet" href="https://fonts.googleapis.com/css2?family=Open+Sans:wght@400;600;700&display=swap">
<style>
  :root {
    --stage: #232323;
    --card-front: #1f1f22;
    --card-back-deep: #2b2b2e;
    --card-back-light: #4a4a4e;
    --gold: #e0a93a;
    --gold-light: #f3cf6e;
    --gold-dark: #b9852a;
    --silver: #d4d6da;
    --white: #f4f4f4;
  }
  * { margin: 0; padding: 0; box-sizing: border-box; }
  html, body { width: 1200px; height: 780px; overflow: hidden; background: var(--stage); }
  body { font-family: "Open Sans", Arial, sans-serif; position: relative; }

  .card {
    position: absolute;
    top: 110px;
    width: 340px;
    height: 560px;
    border-radius: 22px;
    overflow: hidden;
    box-shadow: 0 18px 40px rgba(0,0,0,.55);
  }

  /* Back */
  .card-back { left: 230px; }
  .back-pattern {
    position: absolute; inset: 0;
    background: linear-gradient(135deg, var(--card-back-light) 0%, var(--card-back-deep) 38%, #1c1c1e 100%);
  }
  .back-corner-name {
    position: absolute; top: 22px; right: 22px;
    font-size: 9px; font-weight: 600; letter-spacing: .12em;
    color: var(--gold); text-transform: uppercase; text-align: right; line-height: 1.4;
  }

  /* Front */
  .card-front { left: 630px; background: var(--card-front); }
  .brand {
    position: absolute; top: 92px; left: 0; right: 0;
    display: flex; flex-direction: column; align-items: center; gap: 14px;
  }
  .brand-square { width: 34px; height: 34px; background: var(--gold); }
  .brand-name {
    color: var(--gold); font-weight: 600; font-size: 18px;
    letter-spacing: .14em; text-transform: uppercase; text-align: center; line-height: 1.35;
  }

  .person { position: absolute; top: 300px; left: 0; right: 0; text-align: center; }
  .person-name { font-size: 30px; font-weight: 700; letter-spacing: .01em; }
  .person-first { color: var(--silver); }
  .person-last { color: var(--gold); }
  .person-role { color: var(--white); font-size: 13px; font-weight: 600; margin-top: 2px; }

  .dot-row { position: absolute; left: 0; width: 340px; height: 30px; }
  .dot-row-contact { top: 368px; }
  .dot-row-address { top: 472px; }

  .contact-lines {
    position: absolute; top: 404px; left: 0; right: 0;
    text-align: center; color: var(--white); font-size: 13px; line-height: 1.5;
  }
  .address-lines {
    position: absolute; top: 508px; left: 0; right: 0;
    text-align: center; color: var(--white); font-size: 13px; line-height: 1.5;
  }
</style>
</head>
<body>

<section class="card card-back" aria-label="Card back">
  <div class="back-pattern" role="img" aria-label="Repeating tonal monogram pattern over deep grey, brighter at the upper left"></div>
  <div class="back-corner-name">Renwick Tolliver<br>Construction</div>
</section>

<section class="card card-front" aria-label="Card front">
  <div class="brand">
    <span class="brand-square"></span>
    <div class="brand-name">Renwick Tolliver<br>Construction</div>
  </div>

  <div class="person">
    <div class="person-name"><span class="person-first">Lionel</span> <span class="person-last">Ashby</span></div>
    <div class="person-role">Managing Director</div>
  </div>

  <svg class="dot-row dot-row-contact" viewBox="0 0 340 30" aria-hidden="true">
    <defs>
      <linearGradient id="goldGrad" x1="0" y1="0" x2="1" y2="1">
        <stop offset="0" stop-color="#f3cf6e"/><stop offset="1" stop-color="#b9852a"/>
      </linearGradient>
    </defs>
    <g fill="url(#goldGrad)">
      <circle cx="30" cy="15" r="2"/><circle cx="42" cy="15" r="2.6"/><circle cx="55" cy="15" r="3.2"/>
      <circle cx="69" cy="15" r="4"/><circle cx="84" cy="15" r="4.8"/><circle cx="100" cy="15" r="5.6"/>
      <circle cx="118" cy="15" r="6.4"/>
      <circle cx="142" cy="15" r="11"/><circle cx="170" cy="15" r="11"/><circle cx="198" cy="15" r="11"/>
      <circle cx="222" cy="15" r="6.4"/><circle cx="240" cy="15" r="5.6"/><circle cx="256" cy="15" r="4.8"/>
      <circle cx="271" cy="15" r="4"/><circle cx="285" cy="15" r="3.2"/><circle cx="298" cy="15" r="2.6"/>
      <circle cx="310" cy="15" r="2"/>
    </g>
    <g fill="none" stroke="#1f1f22" stroke-width="1.4" stroke-linecap="round">
      <path d="M137 10c0 6 4 10 10 10l1.5-2-2.5-2-1.5 1c-2-1-3.5-2.5-4.5-4.5l1-1.5-2-2.5z" fill="#1f1f22"/>
      <rect x="164" y="10" width="12" height="9" rx="1"/>
      <path d="M164 11l6 4.5 6-4.5"/>
      <circle cx="198" cy="15" r="6"/>
      <path d="M192 15h12M198 9c-3 3-3 9 0 12M198 9c3 3 3 9 0 12"/>
    </g>
  </svg>

  <div class="contact-lines">
    <div>0782 225 4961</div>
    <div>info@renwick-tolliver.co.uk</div>
    <div>www.renwick-tolliver.co.uk</div>
  </div>

  <svg class="dot-row dot-row-address" viewBox="0 0 340 30" aria-hidden="true">
    <g fill="url(#goldGrad)">
      <circle cx="40" cy="15" r="2"/><circle cx="54" cy="15" r="2.6"/><circle cx="69" cy="15" r="3.2"/>
      <circle cx="85" cy="15" r="4"/><circle cx="102" cy="15" r="4.8"/><circle cx="120" cy="15" r="5.6"/>
      <circle cx="140" cy="15" r="6.4"/>
      <circle cx="170" cy="15" r="11"/>
      <circle cx="200" cy="15" r="6.4"/><circle cx="220" cy="15" r="5.6"/><circle cx="238" cy="15" r="4.8"/>
      <circle cx="255" cy="15" r="4"/><circle cx="271" cy="15" r="3.2"/><circle cx="286" cy="15" r="2.6"/>
      <circle cx="300" cy="15" r="2"/>
    </g>
    <path d="M170 22c-4-5-6-8-6-10.5a6 6 0 0 1 12 0c0 2.5-2 5.5-6 10.5z" fill="#1f1f22"/>
    <circle cx="170" cy="11.5" r="2.2" fill="url(#goldGrad)"/>
  </svg>

  <div class="address-lines">
    <div>Larkspur Road, Elmbridge</div>
    <div>Dorchester, DT4 7QN</div>
  </div>
</section>

</body>
</html>
```